Business Card Design for Marketing Firm

Looking for business card design for higher end marketing firm. Clean but impressionable/trendy. We are a marketing firm that represents manufacturers in the foodservice equipment and supply industry. Our customers are end users such has hotels, restaurants, country clubs, convention centers and casinos as well as distributors of restaurants supplies and equipment, and manufacturers of foodservice equipment and supplies.
Target Market(s)
Hotels, Restaurants, Supply & Equipment Distributors, Foodservice Manufacturers
Industry/Entity Type
Foodservice/Hospitality
Contact Information for Business Card
Name, Title, Contact Number, Email, Website, Social Media, Address
Requirements
Must have
- Clean & Simple but Serious and Impressionable

```html
<!DOCTYPE html>
<html lang="en">
<head>
<meta charset="utf-8">
<title>Orion Service Partners – Business Card</title>
<link href="https://fonts.googleapis.com/css2?family=Montserrat:wght@400;700&display=swap" rel="stylesheet">
<style>
  :root {
    --navy: #2a2874;
    --white: #ffffff;
    --backdrop: #e9e7e4;
    --shadow: rgba(0,0,0,0.18);
  }
  html, body {
    margin: 0;
    width: 1200px;
    height: 834px;
    overflow: hidden;
    background: var(--backdrop);
  }
  .canvas {
    position: relative;
    width: 1200px;
    height: 834px;
  }
  .card {
    position: absolute;
    top: 262px;
    width: 540px;
    height: 309px;
    background: var(--white);
    box-shadow: 0 6px 18px var(--shadow);
    overflow: hidden;
  }
  .card--contact { left: 40px; }
  .card--brand { left: 620px; }

  .wave { position: absolute; inset: 0; }

  .brand {
    position: absolute;
    font-family: "Montserrat", sans-serif;
    font-weight: 700;
    color: var(--navy);
    text-transform: uppercase;
    white-space: nowrap;
  }
  .card--contact .brand {
    left: 30px;
    top: 36px;
    font-size: 14px;
    letter-spacing: 1.5px;
  }
  .card--brand .brand {
    left: 0;
    right: 0;
    top: 118px;
    text-align: center;
    font-size: 28px;
    letter-spacing: 2.5px;
  }

  .socials {
    position: absolute;
    left: 0;
    right: 0;
    top: 200px;
    display: flex;
    justify-content: center;
    gap: 7px;
  }
  .socials__dot {
    width: 13px;
    height: 13px;
    border-radius: 50%;
    background: var(--navy);
  }

  .contact {
    position: absolute;
    right: 34px;
    top: 150px;
    font-family: "Montserrat", sans-serif;
    color: var(--white);
    text-align: right;
  }
  .contact__name {
    font-weight: 700;
    font-size: 17px;
    letter-spacing: 0.5px;
    margin: 0;
  }
  .contact__title {
    font-size: 12px;
    margin: 1px 0 10px;
  }
  .contact__line {
    font-size: 11.5px;
    line-height: 1.45;
    display: flex;
    justify-content: flex-end;
    align-items: center;
    gap: 6px;
  }
  .contact__icon { width: 10px; height: 10px; flex: none; }
  .contact__address { margin-bottom: 6px; }
</style>
</head>
<body>
<div class="canvas">

  <section class="card card--contact">
    <svg class="wave" viewBox="0 0 540 309" preserveAspectRatio="none" aria-hidden="true">
      <path fill="var(--navy)" d="M0,235 C10,170 60,150 150,145 C260,140 330,150 390,120 C440,95 480,60 500,0 L540,0 L540,309 L0,309 Z"/>
      <path fill="none" stroke="var(--white)" stroke-width="2" d="M8,240 C20,178 68,158 155,153 C262,148 336,158 396,128 C448,102 488,64 508,0"/>
    </svg>
    <div class="brand">Orion Service Partners</div>

    <div class="contact">
      <p class="contact__name">DANIEL REYES</p>
      <div class="contact__title">Managing Director</div>
      <div class="contact__address">
        <div class="contact__line">Your address, City</div>
        <div class="contact__line">State, Zip 1234</div>
      </div>
      <div class="contact__line">123 456 789
        <svg class="contact__icon" viewBox="0 0 10 10" aria-hidden="true"><path fill="var(--white)" d="M2,0.5 L4,2.5 L3,3.8 C3.6,5 5,6.4 6.2,7 L7.5,6 L9.5,8 L8,9.5 C4,9 1,6 0.5,2 Z"/></svg>
      </div>
      <div class="contact__line">info@yourmail.com
        <svg class="contact__icon" viewBox="0 0 10 10" aria-hidden="true"><rect x="0.5" y="2" width="9" height="6.5" fill="var(--white)"/><path d="M0.5,2 L5,5.5 L9.5,2" fill="none" stroke="var(--navy)" stroke-width="1"/></svg>
      </div>
      <div class="contact__line">www.yourwebsite.com
        <svg class="contact__icon" viewBox="0 0 10 10" aria-hidden="true"><circle cx="5" cy="5" r="4.5" fill="var(--white)"/><path d="M0.5,5 H9.5 M5,0.5 C2.5,3 2.5,7 5,9.5 M5,0.5 C7.5,3 7.5,7 5,9.5" fill="none" stroke="var(--navy)" stroke-width="0.8"/></svg>
      </div>
    </div>
  </section>

  <section class="card card--brand">
    <div class="brand">Orion Service Partners</div>
    <div class="socials">
      <span class="socials__dot"></span>
      <span class="socials__dot"></span>
      <span class="socials__dot"></span>
      <span class="socials__dot"></span>
      <span class="socials__dot"></span>
      <span class="socials__dot"></span>
    </div>
  </section>

</div>
</body>
</html>
```